Brenvik Systems PowerPoint Template

Project Title: Professional & Functional PowerPoint Template (.potx) – Brenvik Systems Rebrand

Project Overview:
Brenvik Systems has recently undergone a complete rebranding, including a new logo, website, and visual identity. We need a professional, high-end PowerPoint Template (.potx) that reflects our new look while being highly functional for everyday use.

We previously had a design created, but it was built incorrectly (static images, oversized file, no Master Slides). The goal of this project is to take our new aesthetic and build a "workable" template where layouts are controlled by Master Slides and text is easily editable.

Style & Brand Direction:
The template must be an extension of our new website: https://www.brenvik-systems.example/

Aesthetic: Modern, clean, high-tech, and "Industrial Tech."

Color Palette: Please pull the primary blues, greys, and accent colors directly from the website.

Imagery/Graphics: Use clean lines and subtle tech-inspired gradients. Avoid "clutter."

Tone: Innovative, precise, and professional.

Technical Requirements (Crucial)
Format: Must be delivered as a PowerPoint Template file (** .potx **).

Functionality: All layouts must be built using Slide Masters. Users should be able to click "New Slide" and choose from specific layouts.

Native Elements: Do NOT use full-page background images for text areas. Bullet points must use native PowerPoint list functionality (not individual text boxes).

File Size: The template must be optimized and lightweight.

Fonts: Use standard professional fonts or provide the specific web-safe equivalent used on our site (e.g., Montserrat, Open Sans, etc.).

Required Slide Layouts
Please include a minimum of 10–12 Master layouts, including:
*Title Slide (2-3 variations: Dark and Light)
*Agenda/Table of Contents
*Section Header/Divider Slides
*Standard Text/Bullet Slide
*Two-Column Text Slide
*Image + Text Layouts (Left/Right variations)
*Data/Chart Slide (Styled bar/pie charts that match the brand)
*Process/Timeline Slide (Infographic style)
*Section slide

Attachments Provided
Brand Assets (.zip): Contains our new logo in various formats.

Inspiration/Existing PPT: We have attached the previous design created by our web agency. Note: Use this for visual inspiration ONLY. Do not copy the file structure, as it is technically flawed.

Deliverables
Final .potx file.

All used icons or custom graphics in vector format (if applicable).

Instruction note on any specific fonts used.

Target Market(s)

Internal communication and external (investors, customers)

Industry/Entity Type

Semiconductor, Automotive

Requirements
Must have
• A potx file

```html
<!DOCTYPE html>
<html lang="en">
<head>
<meta charset="utf-8">
<title>Brenvik Systems – Presentation Template</title>
<link rel="stylesheet" href="https://fonts.googleapis.com/css2?family=Poppins:wght@400;500;600;700&family=Nunito+Sans:wght@400;600&display=swap">
<style>
:root{
  --page:#ebebed;
  --white:#ffffff;
  --ink:#141414;
  --grey:#6d6d72;
  --blue:#2553f0;
  --blue-mid:#2f7bf5;
  --blue-light:#3aa0f7;
  --line:#d9dbe3;
}
*{box-sizing:border-box;margin:0;padding:0}
html,body{width:1200px;height:1155px;overflow:hidden;background:var(--page)}
body{position:relative;font-family:"Nunito Sans",sans-serif;color:var(--ink)}
.slide{position:absolute;width:514px;height:289px;background:var(--white);overflow:hidden;box-shadow:0 1px 3px rgba(0,0,0,.12)}
.s-welcome{left:62px;top:77px;background:linear-gradient(135deg,#fdfdfd,#f3f4f6)}
.s-agenda{left:624px;top:77px}
.s-who{left:62px;top:428px}
.s-partner{left:624px;top:428px}
.s-intro{left:62px;top:779px;background:linear-gradient(180deg,#2457f0 0%,#3a9cf8 45%,#2350f2 100%)}
.s-service{left:624px;top:779px}
.abs{position:absolute}
.brand{position:absolute;display:flex;align-items:center;gap:4px;font-family:"Poppins",sans-serif;font-weight:700;color:var(--ink);line-height:1;white-space:nowrap}
.brand .mark{background:var(--blue);display:block;flex:none}
.brand-sm{right:26px;top:11px;font-size:15px}
.brand-sm .mark{width:11px;height:11px}
.kicker{position:absolute;left:26px;top:11px;width:48px;height:2px;background:linear-gradient(90deg,var(--blue) 0 58%,transparent 58% 62%,var(--blue-light) 62%)}
.slide-title{position:absolute;left:26px;top:17px;font-family:"Poppins",sans-serif;font-weight:600;font-size:16px;letter-spacing:1px;color:var(--ink)}
.slide-title .accent{color:var(--blue)}
.footer{position:absolute;left:26px;top:276px;font-family:"Poppins",sans-serif;font-size:6.5px;font-weight:500}
.page-no{position:absolute;left:476px;top:273px;width:11px;height:9px;border-radius:1.5px;background:var(--blue);color:#fff;font-family:"Poppins",sans-serif;font-size:5px;font-weight:600;text-align:center;line-height:9px}
.base-bar{position:absolute;left:0;bottom:0;width:100%;height:2px;background:linear-gradient(90deg,var(--blue) 0 75%,var(--blue-light) 75%)}

/* welcome */
.welcome-brand{left:26px;top:45px;font-size:35px;gap:7px}
.welcome-brand .mark{width:26px;height:26px}
.welcome-pre{left:27px;top:93px;font-family:"Poppins",sans-serif;font-weight:500;font-size:16px}
.welcome-title{left:26px;top:113px;font-family:"Poppins",sans-serif;font-weight:700;font-size:24px;line-height:29px;letter-spacing:.5px}
.welcome-title .accent{color:var(--blue)}
.welcome-rule{left:27px;top:180px;width:61px;height:2px;background:var(--blue)}
.welcome-copy{left:27px;top:193px;width:200px;font-size:7.4px;line-height:11.5px;color:#333}
.photo-frame{left:257px;top:33px;width:236px;height:218px;background:var(--blue)}
.photo{position:absolute;left:4px;width:228px;background:linear-gradient(135deg,#3a4656,#1a222c 55%,#6b7a4a)}
.photo.top{top:4px;height:100px}
.photo.bottom{top:110px;height:104px}
.photo-gap{position:absolute;left:0;top:104px;width:236px;height:6px;background:#fff}

/* agenda */
.agenda-table{left:29px;top:50px;width:447px;height:195px;border:1px solid var(--blue)}
.agenda-head{height:26px;background:linear-gradient(180deg,var(--blue),var(--blue-mid));display:flex;align-items:center;color:#fff;font-family:"Poppins",sans-serif;font-weight:600}
.agenda-head .col-title{width:246px;padding-left:52px;font-size:13px}
.agenda-head .col-page{flex:1;text-align:center;font-size:10px;letter-spacing:.5px}
.agenda-divider{position:absolute;left:246px;top:26px;bottom:0;width:1px;background:var(--line)}
.agenda-rows{list-style:none;position:absolute;left:0;top:41px;width:100%}
.agenda-rows li{display:flex;height:29px;font-family:"Poppins",sans-serif;font-size:12.5px;letter-spacing:.5px}
.agenda-rows .item{width:246px;padding-left:39px}
.agenda-rows .num{flex:1;text-align:center}

/* who we are */
.img-back{left:28px;top:63px;width:111px;height:76px;background:var(--blue)}
.img-back2{left:139px;top:150px;width:112px;height:77px;background:var(--blue-mid)}
.wafer{left:33px;top:67px;width:214px;height:154px;background:radial-gradient(ellipse at 45% 60%,#7fd3ee,#2e7fb0 55%,#1d2d44)}
.approach{left:270px;top:72px;width:220px}
.approach h3{font-family:"Poppins",sans-serif;font-weight:600;font-size:10px;color:#555;margin-bottom:6px}
.approach ul{list-style:none}
.approach li{position:relative;padding-left:12px;font-size:7.2px;line-height:13.6px;color:#777}
.approach li::before{content:"";position:absolute;left:0;top:4.5px;width:5px;height:5px;border-radius:50%;background:var(--blue-mid)}

/* partner */
.card{position:absolute;top:77px;width:108px;height:163px;border:1px solid var(--blue-mid);border-radius:4px;padding:33px 7px 0}
.card .icon{position:absolute;left:12px;top:-14px;width:34px;height:34px;border-radius:50%;background:var(--blue);display:flex;align-items:center;justify-content:center}
.card .icon.light{background:var(--blue-light)}
.card h4{font-family:"Poppins",sans-serif;font-weight:600;font-size:10px;color:var(--blue-mid);margin-bottom:5px}
.card p{position:relative;padding-left:7px;font-size:6.2px;line-height:10.8px;color:#333;margin-bottom:10px}
.card p.dot::before{content:"";position:absolute;left:0;top:3px;width:3.5px;height:3.5px;border-radius:50%;background:var(--blue)}

/* intro */
.intro-brand{left:0;right:0;top:97px;justify-content:center;color:#fff;font-size:42px;gap:9px}
.intro-brand .mark{width:32px;height:32px;background:#fff}
.intro-title{left:0;right:0;top:147px;text-align:center;color:#fff;font-family:"Poppins",sans-serif;font-weight:600;font-size:23px;letter-spacing:1.5px}
.intro-rule{left:230px;top:184px;width:54px;height:2px;background:#fff}

/* service */
.service-brand{left:184px;top:121px;font-size:27px;gap:6px}
.service-brand .mark{width:21px;height:21px}
.ring{position:absolute;width:42px;height:42px;border-radius:50%;border:1px solid var(--blue);display:flex;align-items:center;justify-content:center}
.ring span{width:34px;height:34px;border-radius:50%;background:var(--blue);display:flex;align-items:center;justify-content:center}
.ring.light{border-color:var(--blue-light)}
.ring.light span{background:var(--blue-light)}
.feature{position:absolute;width:132px}
.feature h5{font-family:"Poppins",sans-serif;font-weight:600;font-size:7.8px;margin-bottom:4px}
.feature p{font-size:6.4px;line-height:12px;color:#333}
.feature.left{text-align:right}
</style>
</head>
<body>

<!-- Title slide -->
<section class="slide s-welcome">
  <div class="brand welcome-brand"><span class="mark"></span>BRENVIK</div>
  <p class="abs welcome-pre">WELCOME TO</p>
  <h1 class="abs welcome-title"><span class="accent">ENLIGHTENED</span><br>ENGINEERING</h1>
  <div class="abs welcome-rule"></div>
  <p class="abs welcome-copy">For industries driving tech forward, Brenvik is the most advanced laser-based manufacturing partner, unlocking the power of light for cleaner, smarter, more scalable production.</p>
  <div class="abs photo-frame">
    <div class="photo top" role="img" aria-label="Engineers in hard hats reviewing data on control room monitors"></div>
    <div class="photo-gap"></div>
    <div class="photo bottom" role="img" aria-label="Engineer pointing at production charts on a monitor"></div>
  </div>
</section>

<!-- Agenda -->
<section class="slide s-agenda">
  <div class="kicker"></div>
  <h2 class="slide-title" style="color:var(--blue)">AGENDA</h2>
  <div class="brand brand-sm"><span class="mark"></span>BRENVIK</div>
  <div class="abs agenda-table">
    <div class="agenda-head"><span class="col-title">Title</span><span class="col-page">Page Number</span></div>
    <div class="agenda-divider"></div>
    <ul class="agenda-rows">
      <li><span class="item">Introduction</span><span class="num">01</span></li>
      <li><span class="item">About Us</span><span class="num">03</span></li>
      <li><span class="item">Services</span><span class="num">05</span></li>
      <li><span class="item">Solution</span><span class="num">08</span></li>
      <li><span class="item">Contact Us</span><span class="num">10</span></li>
    </ul>
  </div>
  <p class="footer">ALL RIGHTS RESERVED</p>
  <div class="page-no">02</div>
  <div class="base-bar"></div>
</section>

<!-- Who we are -->
<section class="slide s-who">
  <div class="kicker"></div>
  <h2 class="slide-title"><span class="accent">WHO</span> WE ARE</h2>
  <div class="brand brand-sm"><span class="mark"></span>BRENVIK</div>
  <div class="abs img-back"></div>
  <div class="abs img-back2"></div>
  <div class="abs wafer" role="img" aria-label="Laser processing a silicon wafer"></div>
  <div class="abs approach">
    <h3>Our Approach to Meeting Objectives</h3>
    <ul>
      <li>For industries driving tech forward,</li>
      <li>Brenvik is the most advanced laser-based manufacturing partner,unlocking the power of light for cleaner, smarter,</li>
      <li>more scalable production.Using proprietary laser wafer-ing technology, we deliver ultra-clean, ultra-efficient</li>
      <li>wafers that outperform traditional methods in speed, precision, and material yield.</li>
      <li>We deliver manufacturing excellence as a service—no equipment investment, just superior results.</li>
    </ul>
  </div>
  <p class="footer">ALL RIGHTS RESERVED</p>
  <div class="page-no">03</div>
  <div class="base-bar"></div>
</section>

<!-- Partner with precision -->
<section class="slide s-partner">
  <div class="kicker"></div>
  <h2 class="slide-title"><span class="accent">PARTNER</span> WITH PRECISION</h2>
  <div class="brand brand-sm"><span class="mark"></span>BRENVIK</div>

  <div class="card" style="left:26px">
    <div class="icon"><svg width="18" height="14" viewBox="0 0 18 14" fill="#fff"><circle cx="9" cy="4" r="3"/><circle cx="3.5" cy="5" r="2"/><circle cx="14.5" cy="5" r="2"/><path d="M4 13a5 5 0 0 1 10 0z"/><path d="M0 12a3.5 3.5 0 0 1 4-3v4H0zM18 12a3.5 3.5 0 0 0-4-3v4h4z"/></svg></div>
    <h4>Minimize cost</h4>
    <p class="dot">Eliminate expensive tools while reducing labor costs through full automation</p>
    <p class="dot">With $132M in funding from leading VCs and government partners, we're building the backbone of an electrified future.</p>
  </div>
  <div class="card" style="left:144px">
    <div class="icon light"><svg width="18" height="18" viewBox="0 0 18 18" fill="none" stroke="#fff" stroke-width="1.6"><path d="M3 9a6 6 0 0 1 10-4.5M15 9a6 6 0 0 1-10 4.5"/><path d="M13 1.5v3.2h-3.2M5 16.5v-3.2h3.2"/><path d="M6.5 7h5M6.5 9h5M6.5 11h5"/></svg></div>
    <h4>Reduce waste</h4>
    <p class="dot">Achieve 2.2-2.3 wafers per mm with 90% kerf loss reduction</p>
    <p class="dot">With $132M in funding from leading VCs and government partners, we're building the backbone of an electrified future.</p>
  </div>
  <div class="card" style="left:262px">
    <div class="icon"><svg width="18" height="18" viewBox="0 0 18 18" fill="#fff"><rect x="5" y="5" width="8" height="8" rx="1"/><path d="M7 2v3M11 2v3M7 13v3M11 13v3M2 7h3M2 11h3M13 7h3M13 11h3" stroke="#fff" stroke-width="1.4"/></svg></div>
    <h4>Improve quality</h4>
    <p class="dot">Laser-controlled geometry creates ultra-smooth surfaces that enhance device performance</p>
  </div>
  <div class="card" style="left:380px">
    <div class="icon light"><svg width="18" height="16" viewBox="0 0 18 16" fill="none" stroke="#fff" stroke-width="1.6"><path d="M2 14a7 7 0 0 1 14 0"/><path d="M9 14l3-4"/><circle cx="5" cy="3" r="1" fill="#fff"/><circle cx="9" cy="1.5" r="1" fill="#fff"/><circle cx="13" cy="3" r="1" fill="#fff"/></svg></div>
    <h4>Increase yields</h4>
    <p class="dot">Consistent annual returns since inception (2015).</p>
    <p>Long-term track record of performance by the Members.</p>
  </div>

  <p class="footer">ALL RIGHTS RESERVED</p>
  <div class="page-no">04</div>
  <div class="base-bar"></div>
</section>

<!-- Section divider -->
<section class="slide s-intro">
  <div class="brand intro-brand"><span class="mark"></span>BRENVIK</div>
  <h2 class="abs intro-title">INTRODUCTION</h2>
  <div class="abs intro-rule"></div>
</section>

<!-- Our service -->
<section class="slide s-service">
  <div class="kicker"></div>
  <h2 class="slide-title"><span class="accent">OUR</span> SERVICE</h2>
  <div class="brand brand-sm"><span class="mark"></span>BRENVIK</div>

  <div class="brand service-brand"><span class="mark"></span>BRENVIK</div>

  <div class="ring" style="left:155px;top:72px"><span><svg width="16" height="16" viewBox="0 0 16 16" fill="none" stroke="#fff" stroke-width="1.5"><circle cx="8" cy="8" r="6.5"/><rect x="4.5" y="6" width="7" height="5" rx="1"/><path d="M6.5 6V4.5h3V6"/></svg></span></div>
  <div class="ring" style="left:318px;top:72px"><span><svg width="16" height="16" viewBox="0 0 16 16" fill="none" stroke="#fff" stroke-width="1.5"><path d="M2.5 8a5.5 5.5 0 0 1 9.5-3.8M13.5 8A5.5 5.5 0 0 1 4 11.8"/><path d="M12 1.5v3h-3M4 14.5v-3h3"/><path d="M5 10l2.5-2.5 1.5 1.5 2.5-3"/></svg></span></div>
  <div class="ring light" style="left:155px;top:160px"><span><svg width="16" height="16" viewBox="0 0 16 16" fill="#fff"><circle cx="8" cy="5" r="2.5"/><rect x="7" y="7.5" width="2" height="2"/><circle cx="3" cy="11" r="1.5"/><circle cx="13" cy="11" r="1.5"/><circle cx="8" cy="13" r="1.5"/></svg></span></div>
  <div class="ring light" style="left:318px;top:160px"><span><svg width="18" height="14" viewBox="0 0 18 14" fill="#fff"><path d="M4.5 10a3.5 3.5 0 0 1 .4-7 4.5 4.5 0 0 1 8.4 1.5A3 3 0 0 1 13.5 10z"/><path d="M9 10v3M6 13h6" stroke="#fff" stroke-width="1.2"/></svg></span></div>

  <div class="feature left" style="left:14px;top:74px">
    <h5>Focused Portfolio</h5>
    <p>We prioritize a smaller portfolio to maximize returns for each Investment.</p>
  </div>
  <div class="feature" style="left:368px;top:66px">
    <h5>Efficient Processes</h5>
    <p>BVSF employs internal due diligence and document review procedures to ensure cost-effective and timely execution of opportunities.</p>
  </div>
  <div class="feature left" style="left:14px;top:162px">
    <h5>Problem-Solving Strategy</h5>
    <p>Our approach is centered on addressing challenges and/or supporting milestones to unlock each company's full potential</p>
  </div>
  <div class="feature" style="left:368px;top:162px">
    <h5>Robust Network</h5>
    <p>We leverage our established network of professionals and investment partners to explore new opportunities.</p>
  </div>

  <p class="footer">ALL RIGHTS RESERVED</p>
  <div class="page-no">06</div>
  <div class="base-bar"></div>
</section>

</body>
</html>
```